LED strip light bag design

We are brivolta lighting, a LED strip manufacturer in China, We need a packaging design for our LED strip light, as the strip market is full of standard package, so we want to make our package special, and use color orange, black and grey

Target Market(s)

USA, Europe

Contact Information for Business Card

Mason Walsh
Director
Shenzhen Brivolta Lighting Co., Ltd.
Add: 3F, Kaiwen Ind. Zone, Dapu Rd, Hexing, Shenzhen 518207 China
Tel: +86-139-4820 6637 Fax: +86-755-28493016
E-mail: mason.walsh@brivolta-example.com

Font styles to use
Sans Serif
Other font styles liked:
• Tw Cen MT Condensed

Colors

Designer to choose only greyscale colors for use in the design.

Requirements
Must have
• Must have instructions of how to use the strip and CAUTION
• Must have CE, RoHS UL, trash can, ISO9001 logo
Nice to have
• Nice to have a back ground pictures with a strip drawing.

```html
<!DOCTYPE html>
<html lang="en">
<head>
<meta charset="utf-8">
<title>Brivolta LED Strip Light – Bag 215×240mm</title>
<link href="https://fonts.googleapis.com/css2?family=Barlow:wght@400;500;600&family=Barlow+Condensed:wght@500&display=swap" rel="stylesheet">
<style>
  :root {
    --page: #ffffff;
    --bag: #fbfbfb;
    --bag-edge: #e4e4e4;
    --ink: #1a1a1a;
    --logo-bg: #141414;
    --logo-text: #ffffff;
    --accent-red: #d43c1c;
    --accent-orange: #e0661e;
    --accent-amber: #e9a31d;
    --photo-light: #f6c25a;
    --photo-mid: #d98a1a;
    --badge: #9a9a9a;
  }
  * { box-sizing: border-box; margin: 0; padding: 0; }
  html, body { width: 1200px; height: 785px; overflow: hidden; background: var(--page); }
  body { position: relative; font-family: "Barlow", Arial, sans-serif; color: var(--ink); }

  .bag {
    position: absolute;
    top: 140px;
    width: 490px;
    height: 590px;
    background: var(--bag);
    border: 1px solid var(--bag-edge);
  }
  .bag--front { left: 70px; }
  .bag--back { left: 637px; }

  .brand {
    position: absolute;
    display: flex; align-items: center; gap: 8px;
    background: var(--logo-bg);
    color: var(--logo-text);
    font-weight: 600;
    letter-spacing: 0.02em;
  }
  .brand__dot { border-radius: 50%; background: var(--accent-orange); }

  .title { position: absolute; font-weight: 500; line-height: 1; }
  .title span { display: block; }
  .title .t1 { color: var(--accent-red); }
  .title .t2 { color: var(--accent-orange); }
  .title .t3 { color: var(--accent-amber); }

  .strip-photo {
    position: absolute;
    border-radius: 6px;
    background: radial-gradient(ellipse at center, var(--photo-light) 0%, var(--photo-mid) 100%);
  }

  /* front */
  .bag--front .brand { left: 65px; top: 108px; width: 155px; height: 34px; padding-left: 8px; font-size: 20px; }
  .bag--front .brand__dot { width: 18px; height: 18px; }
  .bag--front .title { left: 92px; top: 165px; font-size: 50px; }
  .bag--front .title span + span { margin-top: 3px; }
  .bag--front .strip-photo { left: 236px; top: 160px; width: 215px; height: 350px; }
  .tagline {
    position: absolute; left: 95px; top: 405px;
    font-family: "Barlow Condensed", Arial, sans-serif;
    font-size: 12px; line-height: 14px; letter-spacing: 0.2em; font-weight: 500;
  }

  /* back */
  .bag--back .brand { left: 73px; top: 102px; width: 110px; height: 26px; padding-left: 6px; font-size: 15px; gap: 6px; }
  .bag--back .brand__dot { width: 13px; height: 13px; }
  .bag--back .title { left: 93px; top: 142px; font-size: 32px; }
  .bag--back .title span + span { margin-top: 1px; }
  .label-box { position: absolute; left: 96px; top: 250px; width: 155px; height: 97px; border: 1.5px solid var(--ink); }
  .bag--back .strip-photo { left: 275px; top: 93px; width: 148px; height: 230px; }

  .caution { position: absolute; left: 60px; top: 360px; width: 260px; }
  .caution__icon { position: absolute; left: 0; top: 4px; }
  .caution__head { margin-left: 33px; font-size: 12px; font-weight: 600; line-height: 12px; }
  .caution__sub { margin-left: 33px; font-size: 6.5px; line-height: 8px; }
  .attention { margin-top: 8px; margin-left: 35px; font-size: 6.5px; line-height: 8.2px; width: 240px; }
  .attention ol { list-style: none; }
  .attention li { padding-left: 9px; text-indent: -9px; }

  .marks { position: absolute; left: 318px; top: 370px; width: 80px; height: 110px; }
  .marks .badge { position: absolute; border: 1.5px solid var(--badge); }
</style>
</head>
<body>

  <section class="bag bag--front" aria-label="Bag front">
    <div class="brand"><span class="brand__dot"></span>BRIVOLTA</div>
    <h1 class="title"><span class="t1">LED</span><span class="t2">STRIP</span><span class="t3">LIGHT</span></h1>
    <div class="strip-photo" role="img" aria-label="Photo of a coiled glowing amber LED strip reel"></div>
    <p class="tagline">PROFFESIONAL<br>LIGHTING<br>QUALITY</p>
  </section>

  <section class="bag bag--back" aria-label="Bag back">
    <div class="brand"><span class="brand__dot"></span>BRIVOLTA</div>
    <h2 class="title"><span class="t1">LED</span><span class="t2">STRIP</span><span class="t3">LIGHT</span></h2>
    <div class="label-box" aria-label="Product label area"></div>
    <div class="strip-photo" role="img" aria-label="Photo of a coiled glowing amber LED strip reel"></div>

    <div class="caution">
      <svg class="caution__icon" width="24" height="24" viewBox="0 0 24 24" aria-hidden="true">
        <circle cx="12" cy="12" r="10.5" fill="none" stroke="#1a1a1a" stroke-width="1.5"/>
        <path d="M9 7 C7 10 7 12 9 12 C11 12 11 10 9 7Z M15 12 C13 15 13 17 15 17 C17 17 17 15 15 12Z" fill="#1a1a1a"/>
        <line x1="5" y1="19" x2="19" y2="5" stroke="#1a1a1a" stroke-width="1.5"/>
      </svg>
      <p class="caution__head">CAUTION</p>
      <p class="caution__sub">THIS BAG CONTAINS MOISTURE<br>AND ELECTROSTATIC SENSITIVE DEVICES</p>
      <div class="attention">
        <p>ATTENTION:</p>
        <ol>
          <li>1. STORAGE TEMPEREATURE -40-80ºC<br>&nbsp;&nbsp;&nbsp;OPERATING TEMPEREATURE -40-80ºC</li>
          <li>2. INSTALLATION SURFACE MUST BE SMOOTH, CLEAN AND DRY.</li>
          <li>3. THE PART OF LED COMPONENTS CAN NOT BE FIXED<br>&nbsp;&nbsp;&nbsp;ON THE SURFACE OF THE SHARP EDGE.</li>
          <li>4. STRIP SHOULD NOT BE COLLIDED OR SRUSHED.</li>
          <li>5. STRIP CAN BE CUT FOLLOWING THE CUTTING LINES</li>
          <li>6. THE LED STRIPS, MUST NOT EXCEED 5 METERS,<br>&nbsp;&nbsp;&nbsp;WHEN USED IN A DC SERIES CIRCUIT.</li>
        </ol>
      </div>
    </div>

    <div class="marks" aria-label="Certification marks">
      <span class="badge" style="left:0;top:0;width:36px;height:56px;"></span>
      <span class="badge" style="left:39px;top:0;width:36px;height:56px;"></span>
      <span class="badge" style="left:4px;top:68px;width:26px;height:40px;"></span>
      <span class="badge" style="left:40px;top:61px;width:34px;height:20px;border-radius:50%;"></span>
      <span class="badge" style="left:46px;top:88px;width:22px;height:18px;border-radius:50%;"></span>
    </div>
  </section>

</body>
</html>
```